Healthy lifestyle Influencer business card

I need your creativity to have a business card that I can leave in all the restaurants, hotels and spas I visit to inform them that I am an influencer specializing in the wellness sector and that I will write a review about them. You can use my instagram photos Lunavita27 or on my website www.piattileggeriorto.it. I would like my business card to impress with its creativity! thank you very much!

Contact Information for Business Card

siteweb, instagram, phone number

Font styles to use
Decorative
Script

Colors
0094D4
00A9DD
6FCCEA
C7EBF8
E9F6FB
59FF00
82FF00
B8FF75
E3FFCB
F4FFEA
FFC000
F8CF3A
FAE287
FDF2CF
FEFAEE
F0912C
F2A743
F7CA91
FBE8D2
FDF5EE
EE7325
F08F49
F5BC92
FAE3D3
FDF4ED
EB3D1F
EC4F4E
F09395
F8D3D4
FCEDEE
E54698
E96AAD
F1A4CE
F9D9EA
FCEFF6

Requirements
Nice to have
• creativity

```html
<!DOCTYPE html>
<html lang="it">
<head>
<meta charset="utf-8">
<title>Orto Leggero – Biglietto da visita</title>
<link rel="stylesheet" href="https://fonts.googleapis.com/css2?family=Great+Vibes&family=Jost:wght@400&family=Roboto:wght@300&display=swap">
<style>
  :root {
    --backdrop: #2b2b2b;
    --front-top: #9cc9bb;
    --front-bottom: #86b6a8;
    --back-top: #f4f4f4;
    --back-bottom: #e3e3e3;
    --ink: #3d3d3d;
    --ink-soft: #555b5a;
    --icon: #8fb3a8;
    --kiwi-green: #8fae3a;
    --kiwi-brown: #9c7a45;
    --handle-dot: #6e9e90;
  }
  * { box-sizing: border-box; margin: 0; padding: 0; }
  html, body { width: 1200px; height: 1138px; overflow: hidden; }
  body { background: var(--backdrop); position: relative; font-family: "Roboto", sans-serif; }

  .card {
    position: absolute;
    left: 273px;
    width: 621px;
    height: 376px;
    border-radius: 14px;
    overflow: hidden;
    box-shadow: 0 4px 10px rgba(0,0,0,.45);
  }
  .card--front { top: 184px; }
  .card--back { top: 606px; background: linear-gradient(180deg, var(--back-top), var(--back-bottom)); }

  .food-grid {
    position: absolute; inset: 0;
    background: linear-gradient(160deg, var(--front-top), var(--front-bottom));
  }

  .brand { position: absolute; text-align: center; color: var(--ink); transform: translateX(-50%); }
  .brand__name { font-family: "Great Vibes", cursive; font-weight: 400; line-height: 1; white-space: nowrap; }
  .brand__tagline { font-family: "Jost", sans-serif; white-space: nowrap; }

  .card--front .brand { left: 310px; top: 140px; }
  .card--front .brand__name { font-size: 66px; }
  .card--front .brand__tagline { font-size: 19px; margin-top: 8px; }

  .card--back .brand { left: 181px; top: 146px; }
  .card--back .brand__name { font-size: 54px; }
  .card--back .brand__tagline { font-size: 15px; margin-top: 6px; }

  .handle {
    position: absolute; left: 50%; transform: translateX(-50%);
    display: flex; align-items: center; gap: 10px;
    font-size: 17px; color: var(--ink);
    white-space: nowrap;
  }
  .handle__dot { width: 14px; height: 14px; border-radius: 50%; background: var(--handle-dot); }
  .card--front .handle { top: 325px; }
  .card--back .handle { top: 325px; }

  .owner {
    position: absolute; left: 344px; top: 116px;
    font-family: "Great Vibes", cursive; font-size: 27px; color: var(--ink);
  }
  .contacts { position: absolute; left: 352px; top: 157px; list-style: none; }
  .contacts li {
    display: flex; align-items: center; gap: 12px;
    height: 21px; font-size: 14.5px; color: var(--ink-soft);
  }
  .contacts svg { width: 13px; height: 13px; fill: var(--icon); }
  .vat { position: absolute; left: 352px; top: 227px; font-size: 14.5px; color: var(--ink-soft); }

  .kiwi { position: absolute; }
  .kiwi--top {
    right: 0; top: 0; width: 118px; height: 138px;
    border-bottom-left-radius: 70px;
    background: radial-gradient(circle at 70% 40%, var(--kiwi-green) 0 38%, var(--kiwi-brown) 60%, #6f8f3c 100%);
  }
  .kiwi--bottom {
    left: 0; bottom: 0; width: 118px; height: 136px;
    border-top-right-radius: 70px;
    background: radial-gradient(circle at 30% 60%, var(--kiwi-green) 0 38%, var(--kiwi-brown) 60%, #6f8f3c 100%);
  }
</style>
</head>
<body>

<section class="card card--front">
  <div class="food-grid" role="img" aria-label="Griglia di foto di piatti sani con velatura verde acqua"></div>
  <div class="brand">
    <div class="brand__name">Orto Leggero</div>
    <div class="brand__tagline">Ricette sane per ogni giorno</div>
  </div>
  <div class="handle"><span class="handle__dot"></span>@Lunavita27</div>
</section>

<section class="card card--back">
  <div class="kiwi kiwi--top" role="img" aria-label="Kiwi tagliati a metà con foglie"></div>
  <div class="kiwi kiwi--bottom" role="img" aria-label="Kiwi tagliati a metà con foglie"></div>

  <div class="brand">
    <div class="brand__name">Orto Leggero</div>
    <div class="brand__tagline">Ricette sane per ogni giorno</div>
  </div>

  <div class="owner">Luna Ferretti</div>
  <ul class="contacts">
    <li><svg viewBox="0 0 16 16"><path d="M2 6c0-2 2-3 6-3s6 1 6 3v1h-3V6H5v1H2z M4 8h8l1 5H3z"/></svg>000-0000-0000</li>
    <li><svg viewBox="0 0 16 16"><path d="M1 3h14v10H1z M2 4l6 5 6-5" stroke="#f0f0f0" stroke-width="1"/></svg>ciao@piattileggeriorto.it</li>
    <li><svg viewBox="0 0 16 16"><circle cx="8" cy="8" r="7"/><path d="M1 8h14M8 1v14M3 4h10M3 12h10" stroke="#f0f0f0" stroke-width="0.8" fill="none"/></svg>www.piattileggeriorto.it</li>
  </ul>
  <div class="vat">Partita IVA 04519360271</div>

  <div class="handle"><span class="handle__dot"></span>@Lunavita27</div>
</section>

</body>
</html>
```